Professional Services - letterhead / business cards

The company (velmora partners) will provide services to Investment Funds and large investors in Spain. I have recently chosen a logo that I am attaching.

I would like a simple stationary design that i could use as letter head, business cards and "with compliments" cards.

I am not quite sure which color I will mostly use for the logo, in the email signature I will probably lean towards the white background and grey letters. I am attaching my favourite options.

Target Market(s)

Large Multinationals, Investment funds and Law firms

Industry/Entity Type

Business

Requirements
Must have
• my details are:
Luis R. Abadal
Velmora Partners S.L.
Casa de Torrelumbre
Calle de Vientoalto 27
28014 Madrid
T: +34 (91) 387-2265
M: +34 (646) 819-054
e-mail: labadal@velmorapartners.com

```html
<!DOCTYPE html>
<html lang="en">
<head>
<meta charset="utf-8">
<title>Velmora Partners – Business Card</title>
<link rel="stylesheet" href="https://fonts.googleapis.com/css2?family=Questrial&display=swap">
<style>
  :root {
    --backdrop: #8a8a8a;
    --card-white: #f7f7f5;
    --brand-indigo: #2b2a6e;
    --violet-deep: #34327a;
    --violet-light: #67639f;
    --text-grey: #8c8c8c;
    --rule-grey: #b5b5b5;
  }
  * { margin: 0; padding: 0; box-sizing: border-box; }
  html, body {
    width: 1200px; height: 900px; overflow: hidden;
    background: var(--backdrop);
    font-family: "Questrial", "Century Gothic", sans-serif;
  }
  .stage {
    position: relative; width: 1200px; height: 900px;
  }
  .card {
    position: absolute; width: 540px; height: 308px;
    overflow: hidden;
    box-shadow: 0 10px 24px rgba(0,0,0,.35);
  }
  /* back side */
  .card-back {
    left: 40px; top: 296px;
    background: linear-gradient(115deg, var(--violet-deep) 0%, var(--violet-light) 100%);
  }
  .card-back .watermark-name {
    position: absolute; left: -6px; bottom: -28px;
    font-size: 150px; letter-spacing: -2px;
    color: rgba(255,255,255,.09);
    white-space: nowrap;
  }
  /* front side */
  .card-front {
    left: 620px; top: 296px;
    background: var(--card-white);
    color: var(--brand-indigo);
  }
  .brand-name {
    position: absolute; left: 36px; top: 84px;
    font-size: 30px; letter-spacing: .5px;
    color: var(--brand-indigo);
  }
  .person {
    position: absolute; right: 34px; top: 128px; text-align: right;
  }
  .person-name { font-size: 15px; font-weight: 700; letter-spacing: .5px; }
  .person-role { font-size: 12px; color: var(--text-grey); margin-top: 1px; }
  .rule-top {
    position: absolute; right: 28px; top: 170px; width: 280px;
    height: 1px; background: var(--rule-grey);
  }
  .rule-bottom {
    position: absolute; left: 36px; top: 226px; width: 280px;
    height: 1px; background: var(--rule-grey);
  }
  .contact {
    position: absolute; left: 36px; top: 232px;
    font-size: 12px; line-height: 19px; color: var(--text-grey);
  }
  .contact-line { display: flex; align-items: center; gap: 5px; }
  .contact-line svg { width: 12px; height: 12px; fill: var(--brand-indigo); flex: none; }
  .contact-line .gap { margin-left: 8px; }
</style>
</head>
<body>
<main class="stage">
  <section class="card card-back" aria-label="Card back">
    <div class="watermark-name">velmora</div>
  </section>

  <section class="card card-front" aria-label="Card front">
    <div class="brand-name">velmora partners</div>

    <div class="person">
      <div class="person-name">Luis R. Abadal</div>
      <div class="person-role">Director</div>
    </div>
    <div class="rule-top"></div>

    <div class="rule-bottom"></div>
    <div class="contact">
      <div class="contact-line">Calle de Vientoalto 27 28014 Madrid</div>
      <div class="contact-line">
        <svg viewBox="0 0 12 12" aria-hidden="true"><path d="M1 4c0-2 2-3 5-3s5 1 5 3v1H8V4H4v1H1zM2 6h8l1 5H1z"/></svg>
        +34 (91) 387-2265
        <svg class="gap" viewBox="0 0 12 12" aria-hidden="true"><path d="M3 0h6v12H3zM4 1v6h4V1z"/></svg>
        +34 (646) 819-054
      </div>
      <div class="contact-line">
        <svg viewBox="0 0 12 12" aria-hidden="true"><path d="M0 2h12v8H0zM1 3l5 4 5-4z" fill-rule="evenodd"/></svg>
        labadal@velmorapartners.com
      </div>
    </div>
  </section>
</main>
</body>
</html>
```